business card - Helicopter Flight Services, Flight School, etc.

We need a business card design for a new helicopter service.

We offer Helicopter Flight Services, Aerial Filming & Photography, Flight School, and Helicopter Tours. In that order.

Summit BladeAir, Inc.
Dennis Tollerby
SummitBladeair@Kestmail.com
626-418-7352

Based at the Brenwick Airport in Van Nuys, CA. The final design should communicate integrity and safety. Pictures or logos at your discretion.

Card back side - surprise me.

```html
<!DOCTYPE html>
<html lang="en">
<head>
<meta charset="utf-8">
<title>Summit BladeAir, Inc. — Business Card</title>
<link rel="stylesheet" href="https://fonts.googleapis.com/css2?family=Libre+Baskerville:wght@700&family=Arimo:wght@400&display=swap">
<style>
  :root {
    --canvas-bg: #e9eaec;
    --card-white: #ffffff;
    --sky-top: #e3edf4;
    --sky-mid: #f4f6f8;
    --field-tone: #b9b1a2;
    --tree-tone: #9aa39a;
    --ink: #161616;
    --brand-blue: #2e86c1;
    --band-blue: #3f8fc4;
    --band-blue-light: #66aed6;
    --band-black: #111111;
    --shadow: rgba(0, 0, 0, 0.18);
  }
  * { box-sizing: border-box; margin: 0; padding: 0; }
  html, body { width: 1200px; height: 892px; overflow: hidden; }
  body {
    background: var(--canvas-bg);
    font-family: "Arimo", Arial, sans-serif;
    position: relative;
  }
  .card {
    position: absolute;
    top: 286px;
    width: 540px;
    height: 320px;
    background: var(--card-white);
    box-shadow: 0 10px 28px var(--shadow);
    overflow: hidden;
  }
  .card--front { left: 40px; }
  .card--back { left: 620px; }

  /* Front */
  .front-scene {
    position: absolute;
    inset: 0 0 64px 0;
    background:
      linear-gradient(180deg, transparent 55%, rgba(185,177,162,0.45) 100%),
      radial-gradient(ellipse at 88% 18%, rgba(154,163,154,0.55) 0%, transparent 38%),
      linear-gradient(180deg, var(--sky-top) 0%, var(--sky-mid) 60%, #ece9e3 100%);
  }
  .front-photo {
    position: absolute;
    right: 0; top: 0;
    width: 300px; height: 256px;
    background: linear-gradient(200deg, rgba(154,163,154,0.35) 0%, rgba(185,177,162,0.3) 60%, transparent 100%);
  }
  .front-rule {
    position: absolute;
    left: 0; right: 0;
    bottom: 64px;
    height: 3px;
    background: var(--ink);
  }
  .front-band {
    position: absolute;
    left: 0; right: 0; bottom: 0;
    height: 60px;
    background: linear-gradient(90deg, var(--band-blue) 0%, var(--band-blue-light) 100%);
  }
  .front-content {
    position: absolute;
    left: 34px; top: 28px;
    right: 30px;
  }
  .company-name {
    font-family: "Libre Baskerville", Georgia, serif;
    font-weight: 700;
    font-size: 30px;
    color: var(--ink);
    letter-spacing: 0.2px;
    line-height: 1.05;
  }
  .services {
    font-size: 17px;
    color: var(--brand-blue);
    margin-top: 6px;
  }
  .person-name {
    font-family: "Libre Baskerville", Georgia, serif;
    font-weight: 700;
    font-size: 21px;
    color: var(--brand-blue);
    margin-top: 16px;
  }
  .contact-list {
    list-style: none;
    margin-top: 14px;
  }
  .contact-item {
    display: flex;
    align-items: center;
    gap: 10px;
    font-size: 11.5px;
    color: var(--ink);
    line-height: 1;
    margin-bottom: 6px;
  }
  .contact-icon {
    width: 14px; height: 14px;
    flex: none;
  }

  /* Back */
  .back-content {
    position: absolute;
    left: 0; right: 0; top: 92px;
    text-align: center;
  }
  .back-name {
    font-family: "Libre Baskerville", Georgia, serif;
    font-weight: 700;
    font-size: 34px;
    color: var(--brand-blue);
  }
  .back-services {
    font-size: 18px;
    color: var(--ink);
    margin-top: 12px;
  }
  .back-band {
    position: absolute;
    left: 0; right: 0; bottom: 0;
    height: 44px;
    background: var(--band-black);
  }
  .back-rule {
    position: absolute;
    left: 0; right: 0; bottom: 48px;
    height: 2px;
    background: var(--band-black);
  }
</style>
</head>
<body>

<section class="card card--front" aria-label="Business card front">
  <div class="front-scene"></div>
  <div class="front-photo" role="img" aria-label="Faded photo of a helicopter in flight over trees and open fields"></div>
  <div class="front-rule"></div>
  <div class="front-band"></div>

  <div class="front-content">
    <h1 class="company-name">Summit BladeAir, Inc.</h1>
    <p class="services">Airport · Tour guide · Heliport</p>
    <p class="person-name">Dennis Tollerby</p>
    <ul class="contact-list">
      <li class="contact-item">
        <svg class="contact-icon" viewBox="0 0 14 14" aria-hidden="true"><rect width="14" height="14" rx="2" fill="#161616"/><path d="M4.2 3.2l1.6 0 .7 2-1 .8a6 6 0 0 0 2.5 2.5l.8-1 2 .7v1.6c0 .5-.5.9-1 .8A7.5 7.5 0 0 1 3.4 4.2c-.1-.5.3-1 .8-1z" fill="#fff"/></svg>
        626-418-7352
      </li>
      <li class="contact-item">
        <svg class="contact-icon" viewBox="0 0 14 14" aria-hidden="true"><rect width="14" height="14" rx="2" fill="#161616"/></svg>
        Summit Bladeair Inc.
      </li>
      <li class="contact-item">
        <svg class="contact-icon" viewBox="0 0 14 14" aria-hidden="true"><rect width="14" height="14" rx="2" fill="#161616"/><rect x="3" y="4" width="8" height="6" fill="none" stroke="#fff" stroke-width="1"/><path d="M3 4l4 3.2L11 4" fill="none" stroke="#fff" stroke-width="1"/></svg>
        SummitBladeair@Kestmail.com
      </li>
      <li class="contact-item">
        <svg class="contact-icon" viewBox="0 0 14 14" aria-hidden="true"><rect width="14" height="14" rx="2" fill="#161616"/><path d="M7 2.6a3 3 0 0 1 3 3c0 2.2-3 5.6-3 5.6S4 7.8 4 5.6a3 3 0 0 1 3-3z" fill="#fff"/><circle cx="7" cy="5.6" r="1.1" fill="#161616"/></svg>
        2740 N. Larkspur Ave. Ste.B Van Nuys, CA 91405
      </li>
    </ul>
  </div>
</section>

<section class="card card--back" aria-label="Business card back">
  <div class="back-content">
    <h2 class="back-name">Summit BladeAir, Inc.</h2>
    <p class="back-services">Airport · Tour guide · Heliport</p>
  </div>
  <div class="back-rule"></div>
  <div class="back-band"></div>
</section>

</body>
</html>
```